Brovanek Data Yellow rose letterhead

I have a new logo for my company but in its current form it is too large to be used on letterhead or as a email signature. I need to have the designer use elements from the current logo and create something close to the original but more suited for smaller items.
Updates

I just uploaded a copy of our logo that does not have the weathered affect. Thanks

Reason: More time for revisions

Industry/Entity Type

It Company

Requirements
Must have
• The design must maintain the visual effect of the current logo. It needs to include the yellow rose and the name of the company.
Nice to have
• It would be nice to maintain the stamp theme and incorporate my name, address, phone, email. etc.

```html
<!DOCTYPE html>
<html lang="en">
<head>
<meta charset="utf-8">
<title>Brovanek Data Letterhead</title>
<link href="https://fonts.googleapis.com/css2?family=Arimo:wght@400;700&display=swap" rel="stylesheet">
<style>
  :root {
    --backdrop: #c4c4c4;
    --paper: #ffffff;
    --ink-brown: #4a3b33;
    --rose-yellow: #f7c623;
    --band-light: #ffe07a;
    --band-deep: #f8c21a;
  }
  html, body {
    margin: 0;
    padding: 0;
    width: 848px;
    height: 1200px;
    overflow: hidden;
    background: var(--backdrop);
  }
  .letterhead {
    position: absolute;
    left: 108px;
    top: 153px;
    width: 632px;
    height: 894px;
    background: var(--paper);
    overflow: hidden;
  }
  .brand-name {
    position: absolute;
    right: 150px;
    top: 52px;
    margin: 0;
    font-family: "Arimo", Arial, sans-serif;
    font-weight: 700;
    font-size: 31px;
    line-height: 36px;
    letter-spacing: 3px;
    color: var(--ink-brown);
    white-space: nowrap;
  }
  .brand-mark {
    position: absolute;
    left: 503px;
    top: 14px;
    width: 104px;
    height: 104px;
    border-radius: 50%;
    background: var(--rose-yellow);
  }
  .sender-details {
    position: absolute;
    left: 23px;
    top: 743px;
    margin: 0;
    font-family: "Arimo", Arial, sans-serif;
    font-style: normal;
    font-size: 13.5px;
    line-height: 18.3px;
    color: var(--ink-brown);
  }
  .footer-band {
    position: absolute;
    left: 0;
    bottom: 0;
    width: 632px;
    height: 50px;
    background: linear-gradient(90deg, var(--band-deep), var(--band-light) 50%, var(--band-deep));
  }
</style>
</head>
<body>
  <main class="letterhead">
    <h1 class="brand-name">Brovanek Data</h1>
    <div class="brand-mark"></div>

    <address class="sender-details">
      Marla Quinlan, PhD<br>
      218 NW Cedar Hollow Rd, Ste 1406<br>
      Millbrook, TX 76510<br>
      marla@brovanek-data.com<br>
      1-800-555-0147
    </address>

    <div class="footer-band" role="img" aria-label="Decorative stamp-edge border of brown-outlined scallops over a yellow band"></div>
  </main>
</body>
</html>
```